QuillVane needs a dashboard page designed

Redesign the dashboard shown in the provided images.

There are two images:
- dashboard.png
- dashboard-expanded.png

NOTE: The vocabulary navigation on the left will be a very long list of words 100s, so keep that in mind when you're designing both the vocab navigation and the expanded vocab popup.

In the dashboard.png picture, there needs to be a progress chart showing the word progress like the following: review 1(show it as completed) -> review 2(show the user they are here) -> review 3(unvisited) -> review 4(unvisited)

The do-not-design-this-page.png image is for your reference only. It is not to be designed. Use it to understand the overall look and feel of the website to help you create the best dashboard page possible.
Updates

Need extra days to review

Industry/Entity Type

Education English learning

Number of Pages Required

1 page

Requirements
Must have
• The main navigation and main header cannot change between pages. See the do-not-design page for the main navigateion and header.
Should not have
• Do not add a person profile. We will not have images of our users. Keep the icons in the main navigation as they are.

```html
<!DOCTYPE html>
<html lang="en">
<head>
<meta charset="utf-8">
<title>QuillVane Dashboard</title>
<link href="https://fonts.googleapis.com/css2?family=Lato:wght@400;700;900&display=swap" rel="stylesheet">
<style>
  :root{
    --bg:#f0f0f0;
    --navy:#27313e;
    --blue:#2f62b0;
    --white:#ffffff;
    --text:#2b2f36;
    --muted:#555a61;
    --grey-step:#c8c8c8;
    --band-long:#e8edf2;
    --band-work:#e8f1e6;
    --band-short:#f8f8ea;
    --band-forget:#ededed;
  }
  *{margin:0;padding:0;box-sizing:border-box}
  html,body{width:1200px;height:859px;overflow:hidden;background:var(--bg);font-family:'Lato',sans-serif;color:var(--text)}
  .topbar{position:absolute;left:0;top:0;width:1200px;height:6px;background:var(--navy)}
  .abs{position:absolute;white-space:nowrap}

  .sidebar{position:absolute;left:19px;top:19px;width:245px;height:815px;background:var(--navy);border-radius:13px;color:var(--white)}
  .brand{position:absolute;left:0;width:245px;top:13px;text-align:center;font-size:22px;font-weight:700}
  .filter{position:absolute;left:12px;top:65px;width:81px;height:25px;border:1.5px solid var(--white);font-size:12px;padding:5px 7px;display:flex;justify-content:space-between;align-items:center}
  .expand{position:absolute;left:160px;top:70px;font-size:12.5px;display:flex;align-items:center;gap:8px}
  .pill{position:absolute;left:0;width:47px;height:33px;background:var(--blue);border-radius:0 17px 17px 0;display:flex;align-items:center;justify-content:center}
  .nav-main{position:absolute;left:55px;font-size:16px;transform:translateY(-50%)}
  .chev{position:absolute;left:210px;transform:translateY(-50%)}
  .section{position:absolute;left:78px;font-size:13px;font-weight:700;transform:translateY(-50%);display:flex;align-items:center;gap:6px}
  .current{position:absolute;left:78px;font-size:16px;font-weight:700;transform:translateY(-50%)}
  .word{position:absolute;left:80px;font-size:11px;transform:translateY(-50%)}

  .page-title{left:291px;top:46px;transform:translateY(-50%);font-size:20px;display:flex;align-items:center;gap:12px}
  .tools{left:1060px;top:34px;display:flex;gap:7px}
  .step-label{top:127px;transform:translateY(-50%);font-size:12.5px;color:#444}
  .word-title{left:291px;top:171px;transform:translateY(-50%);font-size:20px;font-weight:700}
  .start-btn{position:absolute;left:452px;top:149px;width:247px;height:43px;background:var(--blue);border-radius:8px;color:var(--white);font-size:12.5px;display:flex;align-items:center;gap:10px;padding-left:15px}
  .card{position:absolute;background:var(--white);border-radius:12px}
  .usage{left:289px;top:218px;width:864px;height:116px;padding:23px 24px;font-size:12.5px;line-height:22px;color:#3a3e44}
  .heading{left:291px;transform:translateY(-50%);font-size:19px;font-weight:700}
  .chart{left:291px;top:404px;width:862px;height:289px}
  .analysis{position:absolute;left:291px;top:757px;font-size:14px;line-height:22px;color:var(--muted)}
</style>
</head>
<body>
<div class="topbar"></div>

<aside class="sidebar">
  <div class="brand">QuillVane</div>
  <div class="filter"><span>All</span>
    <svg width="10" height="6" viewBox="0 0 10 6"><path d="M1 1l4 4 4-4" fill="none" stroke="#fff" stroke-width="1.3"/></svg></div>
  <div class="expand">Expand
    <svg width="11" height="11" viewBox="0 0 11 11"><rect x="1" y="1.5" width="8.5" height="8.5" rx="2" fill="none" stroke="#fff" stroke-width="1"/><path d="M3 5.5l2 2 5-6" fill="none" stroke="#fff" stroke-width="1.1"/></svg></div>

  <div class="pill" style="top:108px">
    <svg width="20" height="20" viewBox="0 0 20 20"><path d="M3 9l7-6 7 6v8H13v-5H7v5H3z" fill="none" stroke="#fff" stroke-width="1.5" stroke-linejoin="round"/></svg></div>
  <div class="nav-main" style="top:123px">WordWise Tutor</div>
  <svg class="chev" style="top:123px" width="10" height="6" viewBox="0 0 10 6"><path d="M1 1l4 4 4-4" fill="none" stroke="#fff" stroke-width="1.3"/></svg>

  <div class="section" style="top:153px;left:55px">
    <svg width="17" height="17" viewBox="0 0 17 17"><circle cx="8.5" cy="8.5" r="7" fill="none" stroke="#fff" stroke-width="1.2" stroke-dasharray="30 4"/><path d="M8.5 4v5l3 2" fill="none" stroke="#fff" stroke-width="1.2"/></svg>
    <span style="margin-left:2px">Short Term Memory</span></div>
  <div class="current" style="top:180px">Grab *</div>
  <div class="section" style="top:208px;left:55px">
    <svg width="17" height="17" viewBox="0 0 17 17"><rect x="4" y="4" width="9" height="9" fill="none" stroke="#fff" stroke-width="1.2"/><rect x="6.5" y="6.5" width="4" height="4" fill="none" stroke="#fff" stroke-width="1"/><path d="M6 1v3M8.5 1v3M11 1v3M6 13v3M8.5 13v3M11 13v3M1 6h3M1 8.5h3M1 11h3M13 6h3M13 8.5h3M13 11h3" stroke="#fff" stroke-width="1"/></svg>
    <span style="margin-left:2px">Working Memory</span></div>

  <div class="word" style="top:237px">Cool Down</div>
  <div class="word" style="top:256px">Crave</div>
  <div class="word" style="top:274px">Go For</div>
  <div class="word" style="top:293px">Go-To</div>
  <div class="word" style="top:312px">In The mood For</div>
  <div class="word" style="top:331px">Sip</div>
  <div class="word" style="top:349px">Soothing</div>
  <div class="word" style="top:368px">Stick With</div>
  <div class="word" style="top:387px">Throw In/Throw On</div>

  <div class="section" style="top:420px;left:55px">
    <svg width="17" height="17" viewBox="0 0 17 17"><rect x="3" y="7.5" width="11" height="8" rx="1.5" fill="none" stroke="#fff" stroke-width="1.3"/><path d="M5.5 7.5V5a3 3 0 0 1 6 0v2.5" fill="none" stroke="#fff" stroke-width="1.3"/><path d="M8.5 10.5v2" stroke="#fff" stroke-width="1.3"/></svg>
    <span style="margin-left:2px">Long Term Memory</span></div>
  <div class="word" style="top:451px">Give It A Try</div>

  <div class="pill" style="top:469px">
    <svg width="22" height="20" viewBox="0 0 22 20"><rect x="2" y="3" width="16" height="14" rx="1.5" fill="none" stroke="#fff" stroke-width="1.2"/><path d="M2 7h16M6 1v4M14 1v4" stroke="#fff" stroke-width="1.2"/><path d="M5 10h2M9 10h2M13 10h2M5 13h2M9 13h2" stroke="#fff" stroke-width="1.2"/><circle cx="17.5" cy="15.5" r="3" fill="#2f62b0" stroke="#fff" stroke-width="1"/><path d="M16 15.5l1 1 2-2" fill="none" stroke="#fff" stroke-width="1"/></svg></div>
  <div class="nav-main" style="top:486px">Daliy English</div>
  <svg class="chev" style="top:486px;left:213px" width="6" height="10" viewBox="0 0 6 10"><path d="M1 1l4 4-4 4" fill="none" stroke="#fff" stroke-width="1.3"/></svg>

  <div class="pill" style="top:513px">
    <svg width="22" height="20" viewBox="0 0 22 20"><path d="M2 9l4-4 3 2 3-2 3 2 5 2M4 11l4 4a1.5 1.5 0 0 0 2-2M8 13l3 3a1.5 1.5 0 0 0 2-2l-3-3M12 14a1.5 1.5 0 0 0 2-2l-3-3M14 12a1.5 1.5 0 0 0 2-2l-4-3" fill="none" stroke="#fff" stroke-width="1.1" stroke-linejoin="round"/><rect x="7" y="1" width="8" height="5" rx="1" fill="none" stroke="#fff" stroke-width="1"/></svg></div>
  <div class="nav-main" style="top:532px">Business</div>
  <svg class="chev" style="top:532px;left:213px" width="6" height="10" viewBox="0 0 6 10"><path d="M1 1l4 4-4 4" fill="none" stroke="#fff" stroke-width="1.3"/></svg>
</aside>

<main>
  <div class="abs page-title">WordWise Tutor
    <svg width="17" height="10" viewBox="0 0 17 10"><path d="M1.5 1.5l7 7 7-7" fill="none" stroke="#2b2f36" stroke-width="2"/></svg></div>

  <div class="abs tools">
    <svg width="28" height="28" viewBox="0 0 28 28"><path d="M14 2l2.5 1 .5 3 2.5 1.5 3-1 2 2-1 3L25 14l1 2.5-2.5 1.5-.5 3-3 .5L17 24l-.5 3h-5L11 24l-2.5-1.5-3 1-2-2 1-3L3 16l-1-2.5L4.5 12 4 9l2.5-2L9 6.5 11 3z" fill="#27313e"/><circle cx="14" cy="14" r="4.5" fill="#f0f0f0"/></svg>
    <svg width="28" height="28" viewBox="0 0 28 28"><circle cx="14" cy="14" r="13.5" fill="#27313e"/><path d="M8 14.5l4 4 8-9" fill="none" stroke="#fff" stroke-width="2.5"/></svg>
    <svg width="28" height="28" viewBox="0 0 28 28"><circle cx="14" cy="14" r="12.5" fill="none" stroke="#27313e" stroke-width="2"/><circle cx="14" cy="11" r="4.5" fill="none" stroke="#27313e" stroke-width="2"/><path d="M6 22.5c2-4 5-5.5 8-5.5s6 1.5 8 5.5" fill="none" stroke="#27313e" stroke-width="2"/></svg>
  </div>

  <svg class="abs" style="left:291px;top:81px" width="612" height="30" viewBox="0 0 612 30">
    <defs><linearGradient id="stepNow" x1="0" x2="1"><stop offset="0" stop-color="#2f62b0"/><stop offset="1" stop-color="#ffffff"/></linearGradient></defs>
    <polygon points="0,0 151,0 156,15 151,30 0,30" fill="#27313e"/>
    <polygon points="151,0 302,0 307,15 302,30 151,30 156,15" fill="url(#stepNow)"/>
    <polygon points="302,0 453,0 458,15 453,30 302,30 307,15" fill="#c8c8c8"/>
    <polygon points="453,0 604,0 609,15 604,30 453,30 458,15" fill="#c8c8c8"/>
    <path d="M151,0 156,15 151,30M302,0 307,15 302,30M453,0 458,15 453,30" fill="none" stroke="#f0f0f0" stroke-width="1.5"/>
  </svg>
  <div class="abs step-label" style="left:291px">Review 1</div>
  <div class="abs step-label" style="left:445px">Review 2</div>
  <div class="abs step-label" style="left:596px">Review 3</div>
  <div class="abs step-label" style="left:747px">Review 4</div>

  <div class="abs word-title">Grab <span style="font-weight:400">*</span></div>
  <div class="start-btn">
    <svg width="12" height="13" viewBox="0 0 12 13"><path d="M0 0l12 6.5L0 13z" fill="#fff"/></svg>
    Start Vocabulary Review Exercise 3</div>

  <div class="card usage">
    The word "greb's most commonly used as a verking to take something quickly rudely in you're running late for school. You dont have time for<br>
    breakfast, so you quickly grab an apple from Tech and rush out the door. As you each the bus stop your friend was andet et grab a coffee aer<br>
    chi Later, when you sat down, your phone starts ringing. You grab it from your bag and answer
  </div>

  <div class="abs heading" style="top:374px">Learning Curve Grach</div>

  <div class="card chart">
    <svg width="862" height="289" viewBox="466 646 1379 463" font-family="Lato, sans-serif">
      <rect x="492" y="691" width="1324" height="37" fill="var(--band-long)"/>
      <rect x="492" y="774" width="1324" height="37" fill="var(--band-work)"/>
      <rect x="492" y="856" width="1324" height="37" fill="var(--band-short)"/>
      <rect x="492" y="936" width="1324" height="39" fill="var(--band-forget)"/>
      <g font-size="15" font-weight="700" fill="#222">
        <text x="496" y="677">Long Term Memory</text>
        <text x="496" y="760">Working Memory</text>
        <text x="496" y="842">Short-Term  Memory</text>
        <text x="496" y="922">Forgotten  Memory</text>
      </g>
      <path d="M669 874 Q725 880 738 948" fill="none" stroke="#bbb" stroke-width="2" stroke-dasharray="7 5"/>
      <path d="M768 692 Q985 710 998 965" fill="none" stroke="#bbb" stroke-width="2" stroke-dasharray="7 5"/>
      <rect x="639" y="874" width="30" height="101" fill="var(--blue)"/>
      <rect x="738" y="692" width="30" height="283" fill="var(--blue)"/>
      <text transform="translate(659 948) rotate(-90)" font-size="14" font-weight="700" fill="#fff">May 18</text>
      <text transform="translate(758 866) rotate(-90)" font-size="14" font-weight="700" fill="#fff">May 19</text>
      <line x1="492" y1="975" x2="1816" y2="975" stroke="#555" stroke-width="1.5"/>
      <g font-size="15" fill="#222" text-anchor="end">
        <text transform="translate(536 992) rotate(-40)">18 May</text>
        <text transform="translate(590 992) rotate(-40)">12:00</text>
        <text transform="translate(657 992) rotate(-40)">19 May</text>
        <text transform="translate(714 992) rotate(-40)">12:00</text>
        <text transform="translate(781 992) rotate(-40)">20 May</text>
        <text transform="translate(844 992) rotate(-40)">12:00</text>
        <text transform="translate(911 992) rotate(-40)">21 May</text>
        <text transform="translate(975 992) rotate(-40)">12:00</text>
        <text transform="translate(1041 992) rotate(-40)">22 May</text>
        <text transform="translate(1109 992) rotate(-40)">12:00</text>
        <text transform="translate(1171 992) rotate(-40)">23 May</text>
        <text transform="translate(1241 992) rotate(-40)">12:00</text>
        <text transform="translate(1303 992) rotate(-40)">24 May</text>
        <text transform="translate(1370 992) rotate(-40)">12:00</text>
        <text transform="translate(1434 992) rotate(-40)">25 May</text>
        <text transform="translate(1502 992) rotate(-40)">12:00</text>
        <text transform="translate(1567 992) rotate(-40)">26 May</text>
        <text transform="translate(1634 992) rotate(-40)">12:00</text>
        <text transform="translate(1701 992) rotate(-40)">27 May</text>
        <text transform="translate(1765 992) rotate(-40)">12:00</text>
      </g>
      <text x="1155" y="1077" font-size="20" font-weight="700" text-anchor="middle" fill="#222">Date Range</text>
    </svg>
  </div>

  <div class="abs heading" style="top:728px">WordWise Tutor Learning Analy</div>
  <div class="analysis">
    Loremiours color mesece edpiscing eft. Namrutan conneco enimibbean, ur dorissimus est, nec finibus nunc dictam ered at equinulle feugiat<br>
    cares an at dolor. Maecenas pretium elique copbus Alquam sit amet euersod metus, quis malesuada scelifeed masse Sed consolex mat lobortis<br>
    gula congue vel. Pellentesque pharetra molestie lessed
  </div>
</main>
</body>
</html>
```